Document Processing Services and Solutions for School Systems

I am looking to design a brochure for both Digital and Paper use. I can supply the written content. Would be looking for an overall design of the brochure with provided content worked into it.

```html
<!DOCTYPE html>
<html lang="en">
<head>
<meta charset="utf-8">
<title>Keystone Docuworks – School Document Management</title>
<link rel="stylesheet" href="https://fonts.googleapis.com/css2?family=Montserrat:wght@400;500;600;700;800&display=swap">
<style>
  :root{
    --navy:#2e3192;
    --gold:#cc9a06;
    --white:#ffffff;
    --ink:#1d1d1d;
    --rule:#b5b5b5;
    --bg:#e6e6e6;
  }
  *{box-sizing:border-box;margin:0;padding:0}
  html,body{width:911px;height:1200px;overflow:hidden;background:var(--bg)}
  body{font-family:"Montserrat",sans-serif;color:var(--ink)}
  .flyer{position:relative;width:911px;height:1200px;background:var(--white);overflow:hidden}
  .abs{position:absolute}
  .hero{position:absolute;left:0;top:0;width:911px;height:491px;background:var(--navy)}
  .hero-photo{position:absolute;left:0;top:0;width:911px;height:491px}
  .brand{left:65px;top:88px;width:320px;text-align:center;color:var(--white)}
  .brand-name{font-size:38px;font-weight:700;letter-spacing:-0.5px;line-height:1}
  .brand-sub{margin-top:14px;display:flex;align-items:center;gap:8px;color:var(--gold);font-size:13px;font-weight:600;letter-spacing:4px}
  .brand-sub::before,.brand-sub::after{content:"";flex:1;height:1.5px;background:var(--gold)}
  .headline{left:65px;top:190px;font-weight:700;line-height:1;color:var(--white)}
  .headline .l1{color:var(--gold);font-size:39px;display:block}
  .headline .l2{font-size:38px;display:block;margin-top:2px}
  .headline .l3{font-size:38px;display:block;margin-top:-2px}
  .headline .l4{font-size:22px;font-weight:400;color:var(--gold);display:block;margin-top:10px}
  .headline .l4 b{font-weight:700}
  .pillars{left:60px;top:372px;display:flex}
  .pillar{width:160px;text-align:center;color:var(--white);font-size:25px;font-weight:700;line-height:1}
  .pillar:nth-child(2){width:152px}
  .pillar svg{display:block;margin:0 auto 14px}
  .intro{left:0;top:491px;width:911px;height:82px;background:var(--gold);color:var(--white);padding:14px 40px 0 65px;font-size:13px;font-weight:600;line-height:16px}
  .section-title{left:65px;top:580px;font-size:29px;font-weight:700;color:var(--navy)}
  .section-title span{color:var(--gold)}
  .section-rule{left:277px;top:596px;width:634px;height:2px;background:var(--rule)}
  .svc-head{height:42px;color:var(--white);font-size:15px;font-weight:600;display:flex;align-items:center;padding-left:14px}
  .svc-head svg{position:absolute;left:0;top:0;z-index:0}
  .svc-head span{position:relative;z-index:1}
  .svc-list{list-style:none}
  .svc-list li{position:relative;height:46px;padding-left:50px;font-size:12px;line-height:14.5px;display:flex;align-items:center}
  .svc-list li svg{position:absolute;left:0;top:4px}
  .why-rule{left:477px;top:843px;width:371px;height:2px;background:var(--navy)}
  .why-tab{left:477px;top:843px;width:371px;height:44px}
  .why-title{left:477px;top:852px;width:371px;text-align:center;color:var(--white);font-size:20px;font-weight:600}
  .card{top:920px;width:84px;height:112px;border:1.5px solid var(--navy);text-align:center;padding-top:15px}
  .card-badge{position:absolute;left:50%;top:-20px;width:34px;height:34px;margin-left:-17px;border-radius:50%;background:var(--navy);display:flex;align-items:center;justify-content:center}
  .card h3{color:var(--gold);font-size:11px;font-weight:500;line-height:11.5px;width:62px;margin:0 auto}
  .card p{margin-top:6px;font-size:6.3px;font-weight:600;line-height:8px;padding:0 4px}
  .cta-band{left:0;top:1043px;width:380px;height:43px}
  .cta-title{left:65px;top:1045px;color:var(--white);font-size:29px;font-weight:600}
  .cta-sub{left:65px;top:1090px;font-size:14.5px;font-weight:700;line-height:19px;width:340px}
  .contact-note{left:477px;top:1058px;font-size:16.5px;font-weight:700;line-height:21px;width:380px}
  .footer-gold{left:0;top:1130px;width:911px;height:70px}
  .contact{top:1155px;display:flex;align-items:center;gap:6px;font-size:14px;font-weight:700;white-space:nowrap}
  .dot{width:18px;height:18px;border-radius:50%;background:var(--navy);display:inline-flex;align-items:center;justify-content:center;flex:none}
  .phone{left:575px;top:1140px;display:flex;align-items:center;gap:10px;color:var(--white);font-size:33px;font-weight:700;white-space:nowrap}
  .phone .dot{width:24px;height:24px}
</style>
</head>
<body>
<main class="flyer">

  <section class="hero">
    <svg class="hero-photo" width="911" height="491" viewBox="0 0 911 491">
      <defs>
        <linearGradient id="photoTone" x1="0" y1="0" x2="1" y2="1">
          <stop offset="0" stop-color="#4a3f38"/>
          <stop offset=".5" stop-color="#7a6a5e"/>
          <stop offset="1" stop-color="#2c2623"/>
        </linearGradient>
      </defs>
      <polygon points="643,0 911,0 911,491 643,491 489,247" fill="var(--white)"/>
      <polygon points="653,0 911,0 911,491 653,491 502,247" fill="url(#photoTone)" role="img" aria-label="Photo of an office worker sorting paper files at a desk in front of a chart-covered board"/>
    </svg>

    <div class="abs brand">
      <div class="brand-name">Keystone</div>
      <div class="brand-sub">DOCUWORKS INC</div>
    </div>

    <h1 class="abs headline">
      <span class="l1">Transform Your</span>
      <span class="l2">School’s Document</span>
      <span class="l3">Management</span>
      <span class="l4">with Our <b>Comprehensive Solutions</b></span>
    </h1>

    <div class="abs pillars">
      <div class="pillar">
        <svg width="56" height="56" viewBox="0 0 56 56" fill="none" stroke="var(--gold)" stroke-width="2.5">
          <circle cx="28" cy="28" r="9"/><circle cx="28" cy="28" r="3.5"/>
          <path d="M11 22a18 18 0 0 1 30-9M45 34a18 18 0 0 1-30 9"/>
          <path d="M41 7v6h-6M15 49v-6h6"/>
        </svg>Streamline
      </div>
      <div class="pillar">
        <svg width="56" height="56" viewBox="0 0 56 56" fill="none" stroke="var(--gold)" stroke-width="2.5">
          <circle cx="28" cy="28" r="15"/>
          <rect x="21" y="27" width="14" height="11" rx="1"/>
          <path d="M24 27v-4a4 4 0 0 1 8 0v4"/>
          <path d="M28 13V3M20 15l-6-8M36 15l6-8M13 28H3M43 28h10M28 43v10M20 41l-6 8M36 41l6 8"/>
        </svg>Secure
      </div>
      <div class="pillar">
        <svg width="56" height="56" viewBox="0 0 56 56" fill="none" stroke="var(--gold)" stroke-width="2.5">
          <circle cx="13" cy="28" r="6"/><circle cx="43" cy="28" r="6"/><circle cx="28" cy="45" r="6"/>
          <path d="M28 4v35M22 10l6-6 6 6M19 28h9M37 28h-9"/>
        </svg>Simplify
      </div>
    </div>
  </section>

  <p class="abs intro">Managing school documents efficiently is crucial for smooth operations, compliance, and productivity. Our document processing services provide innovative solutions tailored for educational institutions, ensuring secure and seamless document and data handling.</p>

  <h2 class="abs section-title">Our <span>Services</span></h2>
  <div class="abs section-rule"></div>

  <div class="abs svc-head" style="left:65px;top:623px;width:338px">
    <svg width="338" height="42" viewBox="0 0 338 42"><polygon points="0,0 318,0 338,42 0,42" fill="var(--navy)"/></svg>
    <span>Document Scanning &amp; Conversion</span>
  </div>
  <ul class="abs svc-list" style="left:65px;top:671px;width:330px">
    <li><svg width="40" height="38" viewBox="0 0 40 38"><polygon points="10,1 30,1 39,19 30,37 10,37 1,19" fill="none" stroke="var(--navy)" stroke-width="1.5"/><circle cx="20" cy="19" r="6" fill="none" stroke="var(--gold)" stroke-width="1.5"/></svg>Convert paper records into digital formats for easy access and storage.</li>
    <li><svg width="40" height="38" viewBox="0 0 40 38"><polygon points="10,1 30,1 39,19 30,37 10,37 1,19" fill="none" stroke="var(--navy)" stroke-width="1.5"/><rect x="12" y="13" width="16" height="12" fill="none" stroke="var(--gold)" stroke-width="1.5"/></svg>High-speed scanning for student records, administrative files, and historical archives.</li>
    <li><svg width="40" height="38" viewBox="0 0 40 38"><polygon points="10,1 30,1 39,19 30,37 10,37 1,19" fill="none" stroke="var(--navy)" stroke-width="1.5"/><path d="M14 10h10l3 3v15H14z M17 17h7M17 21h7" fill="none" stroke="var(--gold)" stroke-width="1.5"/></svg>OCR (Optical Character Recognition) for searchable and editable documents.</li>
  </ul>

  <div class="abs svc-head" style="left:475px;top:623px;width:336px">
    <svg width="336" height="42" viewBox="0 0 336 42"><polygon points="0,0 316,0 336,42 0,42" fill="var(--navy)"/></svg>
    <span style="padding-left:6px">Cloud-Based Document Management</span>
  </div>
  <ul class="abs svc-list" style="left:475px;top:671px;width:380px">
    <li><svg width="40" height="38" viewBox="0 0 40 38"><polygon points="10,1 30,1 39,19 30,37 10,37 1,19" fill="none" stroke="var(--navy)" stroke-width="1.5"/><rect x="15" y="17" width="10" height="8" fill="none" stroke="var(--gold)" stroke-width="1.5"/><path d="M17 17v-3a3 3 0 0 1 6 0v3" fill="none" stroke="var(--gold)" stroke-width="1.5"/></svg>Secure, centralized document storage accessible from anywhere</li>
    <li><svg width="40" height="38" viewBox="0 0 40 38"><polygon points="10,1 30,1 39,19 30,37 10,37 1,19" fill="none" stroke="var(--navy)" stroke-width="1.5"/><circle cx="18" cy="15" r="4" fill="none" stroke="var(--navy)" stroke-width="1.5"/><path d="M11 28a7 7 0 0 1 14 0" fill="none" stroke="var(--navy)" stroke-width="1.5"/><circle cx="27" cy="24" r="3" fill="none" stroke="var(--gold)" stroke-width="1.5"/></svg>Role-based access controls for administrators, teachers, and staff</li>
    <li><svg width="40" height="38" viewBox="0 0 40 38"><polygon points="10,1 30,1 39,19 30,37 10,37 1,19" fill="none" stroke="var(--navy)" stroke-width="1.5"/><path d="M14 10h10l3 3v15H14z M17 17h7M17 21h7" fill="none" stroke="var(--gold)" stroke-width="1.5"/></svg>Automated backups and compliance with educational data security standards.</li>
  </ul>

  <div class="abs svc-head" style="left:65px;top:833px;width:338px">
    <svg width="338" height="42" viewBox="0 0 338 42"><polygon points="0,0 318,0 338,42 0,42" fill="var(--navy)"/></svg>
    <span>Workflow Automation</span>
  </div>
  <ul class="abs svc-list" style="left:67px;top:882px;width:350px">
    <li><svg width="40" height="38" viewBox="0 0 40 38"><polygon points="10,1 30,1 39,19 30,37 10,37 1,19" fill="none" stroke="var(--navy)" stroke-width="1.5"/><rect x="12" y="12" width="16" height="12" fill="none" stroke="var(--gold)" stroke-width="1.5"/><path d="M17 28h6" stroke="var(--gold)" stroke-width="1.5"/></svg>Digitize and streamline approval processes for enrollment, transcripts, and HR forms.</li>
    <li><svg width="40" height="38" viewBox="0 0 40 38"><polygon points="10,1 30,1 39,19 30,37 10,37 1,19" fill="none" stroke="var(--navy)" stroke-width="1.5"/><path d="M14 10h12v18H14z M17 15h6M17 19h6M17 23h6" fill="none" stroke="var(--gold)" stroke-width="1.5"/></svg>Reduce paperwork and improve efficiency with automated workflows.</li>
    <li><svg width="40" height="38" viewBox="0 0 40 38"><polygon points="10,1 30,1 39,19 30,37 10,37 1,19" fill="none" stroke="var(--navy)" stroke-width="1.5"/><circle cx="17" cy="16" r="4.5" fill="none" stroke="var(--gold)" stroke-width="1.5"/><circle cx="24" cy="23" r="4.5" fill="none" stroke="var(--gold)" stroke-width="1.5"/></svg>Integration capable with existing school management systems.</li>
  </ul>

  <div class="abs why-rule"></div>
  <svg class="abs why-tab" width="371" height="44" viewBox="0 0 371 44"><polygon points="65,0 307,0 285,44 87,44" fill="var(--navy)"/></svg>
  <h2 class="abs why-title">Why Choose Us?</h2>

  <div class="abs card" style="left:486px">
    <div class="card-badge"><svg width="18" height="16" viewBox="0 0 18 16" fill="var(--white)"><rect x="1" y="9" width="3" height="6"/><rect x="6" y="6" width="3" height="9"/><rect x="11" y="3" width="3" height="12"/></svg></div>
    <h3>Increased Efficiency</h3>
    <p>Save time with digital workflows and instant document retrieval.</p>
  </div>
  <div class="abs card" style="left:575px">
    <div class="card-badge"><svg width="18" height="16" viewBox="0 0 18 16" fill="var(--white)"><rect x="1" y="9" width="3" height="6"/><rect x="6" y="6" width="3" height="9"/><rect x="11" y="3" width="3" height="12"/></svg></div>
    <h3>Enhanced Security</h3>
    <p style="margin-top:10px">Protect sensitive student and faculty information.</p>
  </div>
  <div class="abs card" style="left:664px">
    <div class="card-badge"><svg width="18" height="18" viewBox="0 0 18 18" fill="none" stroke="var(--white)" stroke-width="1.5"><circle cx="9" cy="7" r="5"/><path d="M2 16h14"/></svg></div>
    <h3 style="width:50px">Cost Savings</h3>
    <p style="margin-top:10px">Reduce paper, printing, and storage costs.</p>
  </div>
  <div class="abs card" style="left:752px">
    <div class="card-badge"><svg width="18" height="18" viewBox="0 0 18 18" fill="none" stroke="var(--white)" stroke-width="1.5"><path d="M3 15C3 7 8 3 15 3c0 7-4 12-12 12zM3 15l7-7"/></svg></div>
    <h3 style="width:50px">Eco-Friendly</h3>
    <p>Minimize your school’s carbon footprint by going digital.</p>
  </div>

  <svg class="abs cta-band" width="380" height="43" viewBox="0 0 380 43"><polygon points="0,0 360,0 380,43 0,43" fill="var(--gold)"/></svg>
  <h2 class="abs cta-title">Get Started Today!</h2>
  <p class="abs cta-sub">Let us help you modernize your document processing system.</p>
  <p class="abs contact-note">Contact us for a free consultation and discover how our solutions can transform your school's document management.</p>

  <svg class="abs footer-gold" width="911" height="70" viewBox="0 0 911 70"><polygon points="554,0 911,0 911,70 524,70" fill="var(--gold)"/></svg>
  <div class="abs contact" style="left:67px">
    <span class="dot"><svg width="10" height="8" viewBox="0 0 10 8" fill="none" stroke="var(--white)" stroke-width="1"><rect x=".5" y=".5" width="9" height="7"/><path d="M.5 .5 5 4.5 9.5 .5"/></svg></span>
    info@keystonedocs.com
  </div>
  <div class="abs contact" style="left:296px">
    <span class="dot"><svg width="12" height="12" viewBox="0 0 12 12" fill="none" stroke="var(--white)" stroke-width="1"><circle cx="6" cy="6" r="5"/><ellipse cx="6" cy="6" rx="2.2" ry="5"/><path d="M1 6h10"/></svg></span>
    www.keystonedocs.com
  </div>
  <div class="abs phone">
    <span class="dot"><svg width="14" height="14" viewBox="0 0 14 14" fill="var(--white)"><path d="M3 1l2.5 3-1.5 1.5c.8 1.8 2.2 3.2 4 4L9.5 8 12.5 10.5 11 13C6 12.5 1.5 8 1 3z"/></svg></span>
    555-014-2290
  </div>

</main>
</body>
</html>
```